Oil Field Service company needs professional business cards

Looking to clean up our current company business cards and look a little more professional. Brenwick Casing Services is a US based company that services the oil field. We deal with engineers, managers and oil rigs....................................................................................................................................................................................................................................................................................................................................................................................................

Target Market(s)

Oil and Gas professionals

Industry/Entity Type

Oil And Gas

Contact Information for Business Card

See attached photo as example

Font styles to use
Sans Serif

Colors
ec1f27

Requirements
Must have
• Company Logo, Name, Title, Cell, Office, Fax, Email.
• See attached photo
Nice to have
• External CRT, Internal CRT, Casing Crews, Torque Turn, Laydown Machine
Should not have
• Do not introduce any new pictures and keep it professional looking

```html
<!DOCTYPE html>
<html lang="en">
<head>
<meta charset="utf-8">
<title>Brenwick Casing Services – Business Card</title>
<link rel="stylesheet" href="https://fonts.googleapis.com/css2?family=Arimo:wght@400;700&family=Oswald:wght@300;400&display=swap">
<style>
  :root {
    --bg: #e6e6e6;
    --card: #f6f6f6;
    --red: #c9201f;
    --navy: #3d4f62;
    --ink: #2f3a45;
    --white: #ffffff;
  }
  * { margin: 0; padding: 0; box-sizing: border-box; }
  html, body { width: 1200px; height: 576px; overflow: hidden; background: var(--bg); }
  .canvas { position: relative; width: 1200px; height: 576px; }
  .card {
    position: absolute; background: var(--card); border-radius: 6px; overflow: hidden;
    box-shadow: 0 2px 4px rgba(0,0,0,.18);
  }
  .card--front { left: 82px; top: 140px; width: 484px; height: 292px; }
  .card--back { left: 602px; top: 138px; width: 481px; height: 291px; }

  .brand { position: absolute; color: var(--navy); font-family: "Arimo", Arial, sans-serif; font-weight: 700; text-align: center; line-height: 1; }
  .brand__name { display: block; letter-spacing: 1px; }
  .brand__line { display: block; letter-spacing: 3px; }

  .card--front .brand { left: 0; right: 0; top: 72px; }
  .card--front .brand__name { font-size: 50px; }
  .card--front .brand__line { font-size: 18px; margin-top: 22px; }

  .services {
    position: absolute; left: 0; right: 0; top: 219px; height: 27px; background: var(--red);
    color: var(--white); font-family: "Arimo", Arial, sans-serif; font-weight: 700; font-size: 13px;
    display: flex; align-items: center; justify-content: center; gap: 7px; letter-spacing: .2px;
  }
  .site-front {
    position: absolute; left: 0; right: 0; top: 261px; display: flex; align-items: center; justify-content: center; gap: 12px;
    font-family: "Arimo", Arial, sans-serif; font-size: 14px; color: var(--ink);
  }
  .site-front__rule { width: 70px; height: 2px; background: var(--red); }

  .card--back .brand { left: 26px; top: 44px; width: 292px; }
  .card--back .brand__name { font-size: 41px; }
  .card--back .brand__line { font-size: 14px; margin-top: 17px; letter-spacing: 2.6px; }

  .person { position: absolute; right: 25px; top: 136px; text-align: right; font-family: "Oswald", sans-serif; color: var(--ink); }
  .person__name { font-size: 21px; font-weight: 400; line-height: 1.1; }
  .person__title { font-size: 12px; font-weight: 300; margin-top: 2px; }
  .person__rule { position: absolute; left: 26px; top: 170px; width: 346px; height: 1px; background: var(--red); }

  .contacts { position: absolute; list-style: none; font-family: "Oswald", sans-serif; font-weight: 300; font-size: 12.5px; color: var(--ink); }
  .contacts li { display: flex; align-items: center; gap: 8px; height: 16px; }
  .contacts svg { width: 10px; height: 10px; fill: var(--red); flex: none; }
  .contacts--phones { left: 28px; top: 199px; }
  .contacts--place { left: 279px; top: 199px; }

  .footer { position: absolute; left: 0; top: 256px; width: 481px; height: 35px; }
  .site-back { position: absolute; left: 254px; right: 0; top: 268px; text-align: center; padding-left: 22px;
    font-family: "Oswald", sans-serif; font-size: 11.5px; color: var(--white); }
</style>
</head>
<body>
<div class="canvas">
  <section class="card card--front">
    <div class="brand"><span class="brand__name">BRENWICK</span><span class="brand__line">CASING SERVICES</span></div>
    <div class="services">
      <span>LAYDOWN MACHINE</span><span>|</span><span>CASING CREW</span><span>|</span><span>MUD TOOL</span><span>|</span><span>TORQUE TURN</span>
    </div>
    <div class="site-front"><span class="site-front__rule"></span><span>www.brenwicksrvs.com</span><span class="site-front__rule"></span></div>
  </section>

  <section class="card card--back">
    <div class="brand"><span class="brand__name">BRENWICK</span><span class="brand__line">CASING SERVICES</span></div>
    <div class="person"><div class="person__name">Cody Harlan</div><div class="person__title">Area Manager</div></div>
    <div class="person__rule"></div>

    <ul class="contacts contacts--phones">
      <li><svg viewBox="0 0 10 10"><path d="M2 0.5l1.8 2-1 1.2c.6 1.3 1.5 2.2 2.6 2.7l1.1-1 2 1.8-1.2 1.8C4.6 8.8 1.2 5.5.3 1.7z"/></svg>(580) 555-0142</li>
      <li><svg viewBox="0 0 10 10"><path d="M0 3.5C0 2 2 1.3 5 1.3S10 2 10 3.5v1H7.6V3.4H2.4v1.1H0zM2 5l1.5-1.2h3L8 5v4H2zm3 .8a1.3 1.3 0 100 2.6 1.3 1.3 0 000-2.6z"/></svg>(580) 555-0187</li>
      <li><svg viewBox="0 0 10 10"><path d="M2.5 0h5v3h-5zM0 3.5h10v4H8V6H2v1.5H0zM2.5 6.5h5V10h-5z"/></svg>(580) 555-0163</li>
    </ul>
    <ul class="contacts contacts--place">
      <li><svg viewBox="0 0 10 10"><path d="M5 0a3.6 3.6 0 00-3.6 3.6C1.4 6.3 5 10 5 10s3.6-3.7 3.6-6.4A3.6 3.6 0 005 0zm0 2.2a1.4 1.4 0 110 2.8 1.4 1.4 0 010-2.8z"/></svg>Redmond, OK 73850</li>
      <li><svg viewBox="0 0 10 10"><path d="M0 2h10L5 5.5zM0 3.2l5 3.5 5-3.5V8H0z"/></svg>codyharlan@brenwicksrvs.com</li>
    </ul>

    <svg class="footer" viewBox="0 0 481 35" aria-hidden="true">
      <rect x="0" y="18" width="266" height="17" fill="var(--red)"/>
      <polygon points="272,0 481,0 481,35 254,35" fill="var(--navy)"/>
    </svg>
    <div class="site-back">www.brenwicksrvs.com</div>
  </section>
</div>
</body>
</html>
```